Tall Fern Roofing Business Card

Need a business card with the logo that was designed here

Contact Information for Business Card

Name, Title, Phone, Email, Website, Company name

```html
<!DOCTYPE html>
<html lang="en">
<head>
<meta charset="UTF-8">
<title>Tall Fern Roofing – Business Card</title>
<link rel="stylesheet" href="https://fonts.googleapis.com/css2?family=Montserrat:wght@700&family=Poppins:wght@400;500&display=swap">
<style>
  :root {
    --brand-blue: #1f76bd;
    --brand-grey: #8f9295;
    --card-white: #ffffff;
    --stage: #e9ebee;
    --ink-dark: #2b2b2b;
  }
  * { box-sizing: border-box; margin: 0; padding: 0; }
  html, body { width: 1200px; height: 900px; overflow: hidden; }
  body {
    background: var(--stage);
    font-family: "Poppins", sans-serif;
    position: relative;
  }
  .card {
    position: absolute;
    left: 250px;
    width: 700px;
    height: 400px;
    overflow: hidden;
    box-shadow: 0 6px 18px rgba(0,0,0,0.18);
  }
  .card--front { top: 35px; background: var(--brand-blue); }
  .card--back { top: 465px; background: var(--card-white); }

  .wordmark {
    display: flex;
    align-items: center;
    gap: 14px;
    font-family: "Poppins", sans-serif;
    font-weight: 500;
    white-space: nowrap;
  }
  .wordmark__square { display: block; flex: none; }
  .card--front .wordmark {
    position: absolute;
    left: 0; right: 0; top: 0; bottom: 0;
    justify-content: center;
    color: var(--card-white);
    font-size: 50px;
  }
  .card--front .wordmark__square { width: 34px; height: 34px; background: var(--card-white); }

  .card--back .wordmark {
    position: absolute;
    right: 40px;
    top: 72px;
    color: var(--brand-blue);
    font-size: 32px;
  }
  .card--back .wordmark__square { width: 22px; height: 22px; background: var(--brand-blue); }

  .holder { position: absolute; left: 48px; top: 62px; }
  .holder__name {
    font-family: "Montserrat", sans-serif;
    font-weight: 700;
    font-size: 27px;
    color: var(--brand-blue);
    letter-spacing: 0.5px;
    line-height: 1.1;
  }
  .holder__title {
    font-size: 19px;
    color: var(--brand-grey);
    letter-spacing: 0.5px;
    line-height: 1.1;
  }

  .contact { position: absolute; left: 86px; top: 196px; list-style: none; }
  .contact__item {
    display: flex;
    align-items: center;
    gap: 12px;
    font-size: 21px;
    color: var(--ink-dark);
    line-height: 30px;
  }
  .contact__icon { width: 22px; height: 22px; flex: none; fill: var(--brand-blue); }

  .wave { position: absolute; left: 0; bottom: 0; width: 700px; height: 260px; }
  .website {
    position: absolute;
    right: 40px;
    bottom: 96px;
    font-size: 18px;
    color: var(--card-white);
  }
</style>
</head>
<body>

  <section class="card card--front" aria-label="Card front">
    <div class="wordmark"><span class="wordmark__square"></span>Tall Fern Roofing</div>
  </section>

  <section class="card card--back" aria-label="Card back">
    <div class="holder">
      <p class="holder__name">MARCUS ELLERY</p>
      <p class="holder__title">MANAGING DIRECTOR</p>
    </div>

    <div class="wordmark"><span class="wordmark__square"></span>Tall Fern Roofing</div>

    <ul class="contact">
      <li class="contact__item">
        <svg class="contact__icon" viewBox="0 0 24 24" aria-hidden="true"><path d="M6.6 10.8a15.1 15.1 0 0 0 6.6 6.6l2.2-2.2a1 1 0 0 1 1-.25 11.4 11.4 0 0 0 3.6.57 1 1 0 0 1 1 1V20a1 1 0 0 1-1 1A17 17 0 0 1 3 4a1 1 0 0 1 1-1h3.5a1 1 0 0 1 1 1c0 1.25.2 2.45.57 3.57a1 1 0 0 1-.25 1z"/></svg>
        044-555 210 384
      </li>
      <li class="contact__item">
        <svg class="contact__icon" viewBox="0 0 24 24" aria-hidden="true"><path d="M2 5h20v14H2z M3.5 6.5 12 13l8.5-6.5" fill="none" stroke="#1f76bd" stroke-width="2"/></svg>
        info@tallfernroofing.com
      </li>
    </ul>

    <svg class="wave" viewBox="0 0 700 260" preserveAspectRatio="none" aria-hidden="true">
      <path d="M0 175 C 180 175, 300 150, 420 95 C 500 55, 560 20, 700 0 L700 40 C 580 60, 500 110, 420 160 C 320 215, 200 230, 0 225 Z" fill="var(--brand-grey)"/>
      <path d="M0 210 C 200 210, 320 185, 430 130 C 520 80, 600 30, 700 20 L700 260 L0 260 Z" fill="var(--brand-blue)"/>
    </svg>

    <p class="website">www.tallfernroofing.com</p>
  </section>

</body>
</html>
```